Business Card Design Project

We are a construction company in Orange County, CA. We need a two sided business card. We would like the back to be our logo with web URL. Front should included Name, title, address, phone, fax and email address.

our address is
627 West Dorrance Blvd, Suite 308
Anaheim, CA 92718

Our logo files are attached.

Construction

```html
<!DOCTYPE html>
<html lang="en">
<head>
<meta charset="utf-8">
<title>Korvel Business Card</title>
<link rel="stylesheet" href="https://fonts.googleapis.com/css2?family=Open+Sans:wght@400;600;700;800&display=swap">
<style>
  :root {
    --brand-blue: #1d4f86;
    --brand-blue-dark: #163e6b;
    --ink: #2b2b2b;
    --ink-soft: #555555;
    --paper: #ffffff;
    --backdrop: #e9ebee;
  }
  * { margin: 0; padding: 0; box-sizing: border-box; }
  html, body {
    width: 1200px; height: 900px; overflow: hidden;
    background: var(--backdrop);
    font-family: "Open Sans", Arial, sans-serif;
  }
  .stage {
    position: relative; width: 1200px; height: 900px;
    display: flex; flex-direction: column; align-items: center; justify-content: center; gap: 60px;
  }
  .card {
    position: relative; width: 560px; height: 320px;
    background: var(--paper); border-radius: 22px; overflow: hidden;
    box-shadow: 0 6px 18px rgba(0,0,0,0.15);
  }

  /* Back side */
  .card-back .wordmark {
    position: absolute; left: 0; right: 0; top: 62px; text-align: center;
    font-size: 92px; font-weight: 800; color: var(--brand-blue);
    letter-spacing: 2px; line-height: 1;
  }
  .card-back .web {
    position: absolute; left: 0; right: 0; top: 162px; text-align: center;
    font-size: 15px; font-weight: 600; color: var(--brand-blue);
  }
  .card-back .band {
    position: absolute; left: 0; right: 0; bottom: 0; height: 92px;
    background: var(--brand-blue);
    display: flex; align-items: center; justify-content: center;
  }
  .card-back .tagline {
    color: var(--paper); font-size: 24px; font-weight: 600; letter-spacing: 6px;
  }

  /* Front side */
  .card-front .side-band { position: absolute; left: 0; top: 0; width: 120px; height: 320px; }
  .card-front .brand {
    position: absolute; left: 118px; top: 22px;
  }
  .card-front .brand-name {
    font-size: 44px; font-weight: 800; color: var(--brand-blue); line-height: 1; letter-spacing: 1px;
  }
  .card-front .brand-tag {
    margin-top: 3px; font-size: 8.5px; font-weight: 600; color: var(--brand-blue); letter-spacing: 1.6px;
  }
  .card-front .person {
    position: absolute; right: 26px; top: 60px; width: 230px; text-align: right;
  }
  .card-front .person-name {
    font-size: 20px; font-weight: 700; color: var(--brand-blue); padding-right: 22px; line-height: 1.2;
  }
  .card-front .rule {
    position: relative; height: 2px; background: var(--brand-blue); margin-top: 2px;
  }
  .card-front .rule::after {
    content: ""; position: absolute; right: 0; top: 0; width: 14px; height: 14px; background: var(--brand-blue);
  }
  .card-front .person-title {
    font-size: 10px; color: var(--ink); padding-right: 28px; margin-top: 2px;
  }
  .card-front .address {
    position: absolute; right: 26px; top: 148px; text-align: right;
    font-size: 15px; font-style: normal; color: var(--brand-blue); line-height: 1.3;
  }
  .card-front .contacts {
    position: absolute; right: 26px; top: 206px; list-style: none;
  }
  .card-front .contacts li {
    display: flex; justify-content: flex-end; align-items: center; gap: 12px;
    font-size: 16px; color: var(--ink); line-height: 24px;
  }
  .card-front .contacts svg { width: 16px; height: 16px; fill: var(--brand-blue); }
</style>
</head>
<body>
<main class="stage">

  <section class="card card-back" aria-label="Card back">
    <div class="wordmark">KORVEL</div>
    <div class="web">www.yourdomain.com</div>
    <div class="band"><span class="tagline">DESIGN • BUILD • DELIVER</span></div>
  </section>

  <section class="card card-front" aria-label="Card front">
    <svg class="side-band" viewBox="0 0 120 320" aria-hidden="true">
      <path d="M0 0 H40 Q100 150 110 320 H0 Z" fill="var(--brand-blue)"/>
      <path d="M40 0 Q100 150 110 320" fill="none" stroke="#111" stroke-width="1.5"/>
    </svg>

    <div class="brand">
      <div class="brand-name">KORVEL</div>
      <div class="brand-tag">DESIGN • BUILD • DELIVER</div>
    </div>

    <div class="person">
      <div class="person-name">Marcus Delaney</div>
      <div class="rule"></div>
      <div class="person-title">GeneralManager</div>
    </div>

    <address class="address">
      627 West Dorrance Blvd, Suite 308<br>
      Anaheim, CA 92718
    </address>

    <ul class="contacts">
      <li>(00) 123-4567-890
        <svg viewBox="0 0 16 16" aria-hidden="true"><path d="M2 6c0-2 2-3 6-3s6 1 6 3v1h-3V6H5v1H2z M4 8h8l1 5H3z"/></svg>
      </li>
      <li>(00) 123-4567-890
        <svg viewBox="0 0 16 16" aria-hidden="true"><path d="M1 1h14v14H1z M3 3v10h10V3z M5 5h6v3H5z M5 9h2v2H5z M9 9h2v2H9z"/></svg>
      </li>
      <li>info@yourdomain.com
        <svg viewBox="0 0 16 16" aria-hidden="true"><path d="M1 6l7-5 7 5v9H1z M3 7v6h10V7L8 10z"/></svg>
      </li>
      <li>www.yourdomain.com
        <svg viewBox="0 0 16 16" aria-hidden="true"><path d="M8 1a7 7 0 1 0 0 14A7 7 0 0 0 8 1z M3 7h10v2H3z M7 2.5h2v11H7z"/></svg>
      </li>
    </ul>
  </section>

</main>
</body>
</html>
```